Oak Ridge Ways Home Page

Redesign the home page -- make it look more attractive and inviting.
Do we need to cut down on the wording? Probably -
Want a cleaner design.
Can go to www.OakRidgeWays.org for the website

```html
<!DOCTYPE html>
<html lang="en">
<head>
<meta charset="utf-8">
<title>Oak Ridge Ways – Home</title>
<link href="https://fonts.googleapis.com/css2?family=Poppins:wght@400;500;600;700;800&family=Heebo:wght@400;500&display=swap" rel="stylesheet">
<style>
:root{
  --blue:#1a3fc4;
  --blue-deep:#0f2ea8;
  --green:#1fa53b;
  --green-light:#7fe36a;
  --ink:#1d1d2b;
  --muted:#4a4a58;
  --page:#f0f2f5;
  --white:#ffffff;
}
*{margin:0;padding:0;box-sizing:border-box}
html,body{width:1200px;height:3490px;overflow:hidden}
body{position:relative;background:var(--white);font-family:'Poppins',sans-serif;color:var(--ink)}
.abs{position:absolute}

/* header */
.login-tab{left:985px;top:14px;width:150px;height:82px;background:var(--green-light);border-radius:0 40px 0 0;font-weight:700;font-size:15px;color:var(--ink);display:flex;align-items:center;justify-content:center;padding-top:8px}
.brand{left:130px;top:22px;display:flex;align-items:center;gap:10px;font-weight:500;font-size:23px;color:var(--blue)}
.brand-mark{width:28px;height:28px;background:var(--blue);border-radius:4px}
.address{left:474px;top:54px;font-family:'Heebo',sans-serif;font-size:11.5px;color:var(--white);white-space:nowrap}
.phone-icon{left:782px;top:40px;width:40px;height:40px;border-radius:50%;background:var(--blue);display:flex;align-items:center;justify-content:center}
.call{left:830px;top:38px;color:var(--white);line-height:1.2}
.call small{display:block;font-size:10px;font-weight:500}
.call strong{font-size:19px;font-weight:700;letter-spacing:.5px}

/* hero */
.hero{left:0;top:92px;width:1200px;height:616px;background:var(--blue-deep);border-radius:60px 0 60px 60px}
.hero-inner{left:12px;top:110px;width:1188px;height:582px;background:linear-gradient(130deg,#1a3bc0,#1d4ad0);border-radius:50px 0 50px 50px}
.nav{display:flex;gap:50px;font-size:16.5px;font-weight:500;color:var(--white)}
.hero-art{left:68px;top:195px;width:558px;height:445px;border-radius:40px;background:linear-gradient(135deg,#f4f4f4,#d9d9d9)}
.play{left:542px;top:567px;width:48px;height:48px;border-radius:50%;background:var(--green);display:flex;align-items:center;justify-content:center}
.hero-copy{left:670px;top:298px;color:var(--white)}
.hero-copy .eyebrow{font-size:13px;font-weight:500}
.hero-copy h1{font-size:43px;font-weight:400;line-height:52px;margin-top:14px}
.hero-copy h1 b{font-weight:800}
.hero-copy .stat{font-size:15px;font-weight:600;margin-top:22px}
.btn{display:inline-flex;align-items:center;gap:18px;height:54px;padding:0 26px 0 5px;border-radius:30px;font-size:15px;font-weight:600;color:var(--white)}
.btn .dot{width:44px;height:44px;border-radius:50%;background:var(--white);display:flex;align-items:center;justify-content:center}
.btn.green{background:var(--green)}
.btn.blue{background:var(--blue)}
.btn.outline{background:var(--white);border:2px solid var(--green);color:var(--green);height:56px}
.btn.outline .dot{background:var(--green)}
.hero-copy .btn{margin-top:24px}

/* pricing */
.pricing{left:0;top:708px;width:1200px;height:600px;background:var(--page)}
.sec-title{width:1200px;left:0;text-align:center;font-size:32px;font-weight:400;color:var(--blue)}
.sec-title b{font-weight:700}
.sec-mark{width:60px;height:16px;left:570px}
.card{top:894px;width:458px;height:317px;background:var(--white);border-radius:18px;box-shadow:0 4px 14px rgba(0,0,0,.1);overflow:hidden;display:flex}
.card .band{width:97px;height:100%;display:flex;align-items:center;justify-content:center}
.card .band span{transform:rotate(-90deg);color:var(--white);font-size:52px;font-weight:800;white-space:nowrap}
.card .body{flex:1;text-align:center;padding-top:22px}
.card h3{font-size:15px;font-weight:600;line-height:30px}
.price{display:flex;align-items:center;justify-content:center;gap:10px;margin-top:4px}
.price small{font-size:12px;font-weight:700}
.price strong{font-size:40px;font-weight:700;line-height:52px}
.card .get{font-size:13px;font-weight:600;margin-top:2px}
.card ul{list-style:none;font-family:'Heebo',sans-serif;font-size:12.5px;line-height:24px;color:var(--ink);margin-top:2px}
.card.gold ul{line-height:19px;margin-top:4px}
.card .btn{margin-top:12px;height:52px}

/* steps */
.step-text{width:420px}
.step-text h2{font-size:27px;font-weight:600;line-height:36px;color:var(--ink)}
.step-text ol{list-style:none;font-family:'Heebo',sans-serif;font-size:13px;line-height:24px;color:var(--muted);margin-top:16px}
.step-text li{display:flex;gap:8px}
.step-text li b{color:var(--blue);font-weight:500}
.step-text .btn{margin-top:16px}
.photo{width:469px;height:366px;border-radius:40px}
.badge{width:78px;height:78px;border-radius:50%;background:var(--blue);border:4px solid var(--white);color:var(--white);font-size:12.5px;font-weight:600;text-align:center;padding-top:15px}
.badge svg{display:block;margin:6px auto 0}

/* footer */
.footer{left:0;top:3143px;width:1200px;height:347px;background:linear-gradient(130deg,var(--blue-deep),var(--blue));border-radius:60px 60px 0 0}
.foot-brand{left:0;width:1200px;top:3238px;display:flex;justify-content:center;align-items:center;gap:16px;color:var(--white);font-size:38px;font-weight:500}
.foot-brand i{width:60px;height:60px;background:var(--white);border-radius:8px;display:block}
.social{left:537px;top:3387px;display:flex;gap:10px}
.social i{width:38px;height:38px;border-radius:50%;background:var(--green);display:block}
.copy{left:0;width:1200px;top:3448px;text-align:center;color:var(--white);font-size:12px;font-weight:500}
</style>
</head>
<body>

<!-- header -->
<svg class="abs" style="left:0;top:0" width="1000" height="96" viewBox="0 0 1000 96"><path d="M85 93 L940 0 Q1000 0 1000 50 L1000 93 Z" fill="#1fa53b"/></svg>
<div class="abs login-tab">LOGIN</div>
<div class="abs brand"><span class="brand-mark"></span>Oak Ridge Ways</div>
<div class="abs address">58 Larch Avenue, Suite 210, Milbrook, Vermont 05601</div>
<div class="abs phone-icon"><svg width="16" height="16" viewBox="0 0 24 24"><path fill="#fff" d="M6.6 10.8a15 15 0 0 0 6.6 6.6l2.2-2.2c.3-.3.7-.4 1-.2 1.1.4 2.3.6 3.6.6.6 0 1 .4 1 1V20c0 .6-.4 1-1 1A17 17 0 0 1 3 4c0-.6.4-1 1-1h3.5c.6 0 1 .4 1 1 0 1.3.2 2.5.6 3.6.1.3 0 .7-.2 1z"/></svg></div>
<div class="abs call"><small>CALL US TODAY</small><strong>(800) 555-0142</strong></div>

<!-- hero -->
<section class="abs hero"></section>
<div class="abs hero-inner"></div>
<nav class="abs nav" style="left:345px;top:130px"><span>Home</span><span>Testimonials</span><span>Max Scores</span><span>FAQ</span><span>Blog</span></nav>
<div class="abs hero-art" role="img" aria-label="Illustration of a thoughtful man imagining a house with +$5000 savings"></div>
<div class="abs play"><svg width="16" height="18" viewBox="0 0 16 18"><path d="M2 1l13 8-13 8z" fill="#fff"/></svg></div>
<div class="abs hero-copy">
  <div class="eyebrow">RECOGNIZED AS</div>
  <h1>The <b>BEST Credit</b> Score<br>Improvement Program</h1>
  <div class="stat">81 AVERAGE POINT IMPROVEMENT</div>
  <a class="btn green"><span class="dot"><svg width="18" height="14" viewBox="0 0 18 14"><path d="M1 7h15M10 1l6 6-6 6" stroke="#1a3fc4" stroke-width="2" fill="none"/></svg></span>GET STARTED</a>
</div>

<!-- pricing -->
<section class="abs pricing"></section>
<svg class="abs sec-mark" style="top:800px" viewBox="0 0 60 16"><path d="M0 16 L40 2 L60 16Z" fill="#1fa53b"/></svg>
<h2 class="abs sec-title" style="top:818px">Our <b>Pricing</b> Plan</h2>

<div class="abs card" style="left:131px">
  <div class="band" style="background:var(--blue)"><span>Silver</span></div>
  <div class="body">
    <h3>Lender's Report, Lender's Scores<br>&amp; Analysis</h3>
    <div class="price"><small>Only</small><strong style="color:var(--blue)">$59.95</strong></div>
    <div class="get">Get Your</div>
    <ul><li>TrueScore® Credit Scores Lenders use</li><li>Complete Credit Score Analysis</li><li>Potential Mortgage and Auto Loan Qualifications</li></ul>
    <a class="btn green"><span class="dot"><svg width="18" height="14" viewBox="0 0 18 14"><path d="M1 7h15M10 1l6 6-6 6" stroke="#1fa53b" stroke-width="2" fill="none"/></svg></span>GET STARTED</a>
  </div>
</div>
<div class="abs card gold" style="left:611px">
  <div class="band" style="background:var(--green)"><span>Gold</span></div>
  <div class="body">
    <h3>Lender's Report, Lender's Scores, Analysis<br>&amp; Steps to Score Improvement</h3>
    <div class="price"><small>Only</small><strong style="color:var(--green)">$79.95</strong></div>
    <div class="get">Get Your</div>
    <ul><li>TrueScore® Credit Scores Lenders use</li><li>Complete Credit Score Analysis</li><li>Potential Mortgage and Auto Loan Qualifications</li><li>Personalized Solutions to Higher TrueScore® Scores</li></ul>
    <a class="btn blue"><span class="dot"><svg width="18" height="14" viewBox="0 0 18 14"><path d="M1 7h15M10 1l6 6-6 6" stroke="#1a3fc4" stroke-width="2" fill="none"/></svg></span>GET STARTED</a>
  </div>
</div>

<!-- how it works -->
<svg class="abs sec-mark" style="top:1380px" viewBox="0 0 60 16"><path d="M0 16 L40 2 L60 16Z" fill="#1fa53b"/></svg>
<h2 class="abs sec-title" style="top:1398px">How <b>It</b> Works</h2>

<div class="abs step-text" style="left:131px;top:1505px">
  <h2>See What Your Lenders See - Get the Same Credit Report and Scores Lenders Use</h2>
  <ol><li><b>01</b><span>As a Certified Credit Counselor, We Provide the Same Credit Report and 3 Scores Used by Mortgage &amp; Auto Lenders</span></li>
  <li><b>02</b><span>Don't be Misled by "Unreliable Internet Credit Scores" - Not Knowing Accurate Scores could Cost You Lots of Money</span></li></ol>
  <a class="btn outline"><span class="dot"><svg width="18" height="14" viewBox="0 0 18 14"><path d="M1 7h15M10 1l6 6-6 6" stroke="#fff" stroke-width="2" fill="none"/></svg></span>LEARN MORE</a>
</div>
<div class="abs photo" style="left:600px;top:1472px;background:linear-gradient(135deg,#3b4a5e,#c98a3a 60%,#e9e2d6)" role="img" aria-label="Photo of a person holding a credit card at a laptop"></div>
<div class="abs badge" style="left:561px;top:1618px">STEP 01<svg width="26" height="16" viewBox="0 0 26 16"><path d="M1 8h22M16 1l7 7-7 7" stroke="#fff" stroke-width="3" fill="none"/></svg></div>

<div class="abs photo" style="left:127px;top:1890px;background:linear-gradient(135deg,#d9d4c6,#a9b08a 50%,#f1eee6)" role="img" aria-label="Photo of a smiling woman with a phone reviewing documents"></div>
<div class="abs badge" style="left:557px;top:2033px">STEP 02<svg width="26" height="16" viewBox="0 0 26 16"><path d="M1 8h22M16 1l7 7-7 7" stroke="#fff" stroke-width="3" fill="none"/></svg></div>
<div class="abs step-text" style="left:652px;top:1940px">
  <h2>Work with the BEST Credit Score Improvement Program</h2>
  <ol><li><b>01</b><span>Oak Ridge Ways Averages an Amazing 81-Point Improvement for all 3 TrueScore Credit Scores</span></li>
  <li><b>02</b><span>Identifies Accounts to Pay Down (by Priority), to Close, to Use, to Open, to Refinance, and to Consolidate</span></li></ol>
  <a class="btn outline"><span class="dot"><svg width="18" height="14" viewBox="0 0 18 14"><path d="M1 7h15M10 1l6 6-6 6" stroke="#fff" stroke-width="2" fill="none"/></svg></span>LEARN MORE</a>
</div>

<div class="abs step-text" style="left:131px;top:2305px">
  <h2>Want to Know Your Potential Mortgage and Auto Loan Qualifications</h2>
  <ol><li><b>01</b><span>Since We Provide the Same TrueScore Scores Lenders Use, We Give You Insight to Your Loan Qualifications</span></li>
  <li><b>02</b><span>See What Mortgage and Auto Loan Options Work Best for you. Don't Wait for a Loan Officer</span></li></ol>
  <a class="btn outline"><span class="dot"><svg width="18" height="14" viewBox="0 0 18 14"><path d="M1 7h15M10 1l6 6-6 6" stroke="#fff" stroke-width="2" fill="none"/></svg></span>LEARN MORE</a>
</div>
<div class="abs photo" style="left:600px;top:2273px;background:linear-gradient(135deg,#5f7a8f,#1b3e8f 50%,#7a6a55)" role="img" aria-label="Photo of a laptop displaying a credit score gauge"></div>
<div class="abs badge" style="left:561px;top:2418px">STEP 03<svg width="26" height="16" viewBox="0 0 26 16"><path d="M1 8h22M16 1l7 7-7 7" stroke="#fff" stroke-width="3" fill="none"/></svg></div>

<div class="abs photo" style="left:127px;top:2690px;background:linear-gradient(135deg,#3a2a1e,#d9b98a 50%,#2b2018)" role="img" aria-label="Photo of a hand holding a credit card"></div>
<div class="abs badge" style="left:557px;top:2834px">STEP 04<svg width="26" height="16" viewBox="0 0 26 16"><path d="M1 8h22M16 1l7 7-7 7" stroke="#fff" stroke-width="3" fill="none"/></svg></div>
<div class="abs step-text" style="left:652px;top:2725px;width:440px">
  <h2>Improve Your Purchasing Power by Increasing Your Lender's TrueScore Scores</h2>
  <ol><li><b>01</b><span>Loan Officers Don't Care if You are Paying $100's More on Your Mortgage or Auto Loan Payment - You're Paying It!</span></li>
  <li><b>02</b><span>Most Home and Auto Buyers have Higher Payments because of Less-than-Excellent TrueScore Scores - Usually Less than 760</span></li></ol>
  <a class="btn outline"><span class="dot"><svg width="18" height="14" viewBox="0 0 18 14"><path d="M1 7h15M10 1l6 6-6 6" stroke="#fff" stroke-width="2" fill="none"/></svg></span>LEARN MORE</a>
</div>

<!-- footer -->
<footer class="abs footer"></footer>
<div class="abs foot-brand"><i></i>Oak Ridge Ways</div>
<nav class="abs nav" style="left:345px;top:3339px"><span>Home</span><span>Testimonials</span><span>Max Scores</span><span>FAQ</span><span>Blog</span></nav>
<div class="abs social"><i></i><i></i><i></i></div>
<div class="abs copy">© copyrights 2022 Oak Ridge Ways &nbsp;|&nbsp; All Rights Reserved</div>

</body>
</html>
```